HearthMile business card and stationary design

We are looking for a simple yet elegant design for our mortgage company business card and stationary.

The card should include:
Name (Marcus Pell)
Title (CEO)
Phone Number (555-555-0182)
Address (48 Birchwell Court, Suite 314, Fernmoor, ZZ 00000)
Email (email@hearthmile.example)
"NMLS" i.e. (NMLS 61947)
"Company NMLS" (Company NMLS 274615)

Contact Information for Business Card

See above

```html
<!DOCTYPE html>
<html lang="en">
<head>
<meta charset="utf-8">
<title>HearthMile business cards</title>
<link href="https://fonts.googleapis.com/css2?family=Montserrat:wght@600;700&family=Arimo:wght@400;500&display=swap" rel="stylesheet">
<style>
  :root {
    --sky: #05aeea;
    --navy: #1b2431;
    --paper: #ffffff;
    --ground: #2b2b2b;
    --ink: #1b2431;
  }
  * { box-sizing: border-box; margin: 0; padding: 0; }
  html, body { width: 1200px; height: 1015px; overflow: hidden; }
  body { background: var(--ground); position: relative; font-family: "Arimo", Arial, sans-serif; }
  .card { position: absolute; width: 560px; height: 320px; overflow: hidden; }
  .card-front { left: 90px; top: 110px; background: var(--paper); }
  .card-back { left: 550px; top: 560px; background: var(--sky); }

  .wordmark { font-family: "Montserrat", Arial, sans-serif; font-weight: 700; letter-spacing: 1px; }
  .card-front .wordmark { position: absolute; left: 0; right: 0; top: 118px; text-align: center; font-size: 62px; color: var(--ink); }
  .front-web { position: absolute; right: 60px; bottom: 50px; font-size: 15px; color: var(--ink); letter-spacing: .5px; }
  .accent { color: var(--sky); }

  .back-shape { position: absolute; inset: 0; width: 560px; height: 320px; }
  .card-back .wordmark { position: absolute; left: 26px; top: 40px; font-size: 34px; color: var(--paper); }
  .licences { position: absolute; right: 26px; top: 26px; text-align: right; color: var(--paper); font-size: 14px; line-height: 1.35; letter-spacing: .5px; }
  .holder { position: absolute; left: 248px; top: 150px; text-align: right; width: 190px; }
  .holder .name { font-family: "Montserrat", Arial, sans-serif; font-weight: 700; font-size: 26px; color: var(--sky); white-space: nowrap; }
  .holder .title { font-size: 16px; color: var(--paper); margin-top: 2px; }
  .address { position: absolute; left: 90px; top: 228px; width: 180px; text-align: right; color: var(--paper); font-size: 14px; line-height: 1.3; font-style: normal; }
  .divider { position: absolute; left: 284px; top: 226px; width: 1px; height: 62px; background: var(--paper); }
  .contact { position: absolute; left: 300px; top: 224px; list-style: none; color: var(--paper); font-size: 14px; line-height: 1.55; }
  .contact li { display: flex; align-items: center; gap: 8px; white-space: nowrap; }
  .contact svg { width: 13px; height: 13px; flex: none; }
</style>
</head>
<body>
  <section class="card card-front" aria-label="Card front">
    <div class="wordmark">HearthMile</div>
    <div class="front-web">www.<span class="accent">hearthmile</span>.example</div>
  </section>

  <section class="card card-back" aria-label="Card back">
    <svg class="back-shape" viewBox="0 0 560 320" aria-hidden="true">
      <polygon points="0,262 300,94 560,86 560,320 0,320" fill="#ffffff"/>
      <polygon points="0,280 306,110 560,102 560,320 0,320" fill="#1b2431"/>
    </svg>
    <div class="wordmark">HearthMile</div>
    <div class="licences">Company NMLS 274615<br>NMLS 61947</div>
    <div class="holder">
      <div class="name">Marcus Pell</div>
      <div class="title">CEO</div>
    </div>
    <address class="address">48 Birchwell Court<br>Suite 314 Fernmoor<br>ZZ 00000</address>
    <div class="divider"></div>
    <ul class="contact">
      <li><svg viewBox="0 0 24 24"><path fill="#05aeea" d="M6.6 10.8a15 15 0 0 0 6.6 6.6l2.2-2.2c.3-.3.7-.4 1-.2 1.1.4 2.3.6 3.6.6.6 0 1 .4 1 1V20c0 .6-.4 1-1 1A17 17 0 0 1 3 4c0-.6.4-1 1-1h3.5c.6 0 1 .4 1 1 0 1.3.2 2.5.6 3.6.1.3 0 .7-.2 1z"/></svg><span>555-555-0182</span></li>
      <li><svg viewBox="0 0 24 24"><rect x="2" y="5" width="20" height="14" rx="1" fill="#05aeea"/><path d="M2 6l10 7 10-7" fill="none" stroke="#1b2431" stroke-width="1.6"/></svg><span>email@hearthmile.example</span></li>
      <li><svg viewBox="0 0 24 24" fill="none" stroke="#05aeea" stroke-width="2"><circle cx="12" cy="12" r="9"/><path d="M3 12h18M12 3c3 3 3 15 0 18M12 3c-3 3-3 15 0 18"/></svg><span>www.<span class="accent">hearthmile</span>.example</span></li>
    </ul>
  </section>
</body>
</html>
```